Studyvane - online education agent and consultancy

Online education provider for business to business market needs a dynamic, modern and mobile friendly website. We have the shell view www.quorvana.com but it is boring!
I will need to add courses to the website - Business, Health and Wellbeing, Digital, Aviation.
I am targeting mainly services based industries - so blue collar workers, living in the outer suburbs, will be studying online and most likely from home.
They need to feel safe and secure - we are reputable and importantly can support them all the way to course completion.
What makes us stand out from everyone else - we dont offer any courses - we pick and choose the best courses, with the best providers and only offer quality.
We take the time to find out what the student really wants to achieve and match them with the right education provider.

Target Market(s)

Business to Business - HR managers, People and Culture Managers, employees who are 25+ years currently working wanting to further their careers with accredited qualifications

Industry/Entity Type

Education

Number of Pages Required

5+ page

Font styles to use
Sans Serif

Colors
00a990
acd036
0792cd
a54499
f37122

Requirements
Must have
• Mobile functionality - view on ovulet/ovutab
• Home page
• Courses section
• Contact us
• Payment checkout to be added
Nice to have
• Fresh, inviting, images that reflect the difference we will make - supporting people through the whole journey.
• It needs to be inviting - homely but modern
Should not have
• Black, dark colours

```html
<!DOCTYPE html>
<html lang="en">
<head>
<meta charset="utf-8">
<title>Lumora Online Education</title>
<link href="https://fonts.googleapis.com/css2?family=Roboto:wght@300;400;500;700&family=Roboto+Condensed:wght@400;700&display=swap" rel="stylesheet">
<style>
:root{
  --green:#79b532;
  --green-dark:#5e9a1f;
  --green-deep:#4d8418;
  --teal:#00a990;
  --blue:#0792cd;
  --yellow:#f2b705;
  --red:#e2453c;
  --text:#555;
  --heading:#333;
  --muted:#999;
  --band:#efefef;
  --white:#fff;
}
*{box-sizing:border-box;margin:0;padding:0}
html,body{width:1200px;height:2360px;overflow:hidden}
body{font-family:"Roboto",Arial,sans-serif;color:var(--text);background:var(--white);position:relative}
.wrap{width:1040px;margin:0 auto;position:relative}

/* header */
.topbar{height:120px}
.topbar .wrap{display:flex;align-items:center;justify-content:space-between;height:120px}
.brand{display:flex;align-items:center;gap:14px;font-size:46px;font-weight:700;color:var(--green);letter-spacing:1px}
.brand .dot{width:22px;height:22px;border-radius:50%;background:var(--green)}
.top-contact{display:flex;align-items:center;gap:22px;font-size:15px;color:var(--muted)}
.top-contact span{display:flex;align-items:center;gap:8px}
.ico{width:26px;height:26px;border-radius:50%;background:var(--green);display:inline-flex;align-items:center;justify-content:center}
.search{width:190px;height:34px;border:1px solid #ddd;display:flex;align-items:center;padding:0 10px;justify-content:space-between;color:#bbb;font-size:14px}

.nav{height:68px;background:var(--green)}
.nav ul{list-style:none;display:flex;width:1040px;margin:0 auto;height:68px}
.nav li{flex:1;display:flex;align-items:center;justify-content:center;color:var(--white);font-size:15px;font-weight:500;letter-spacing:1px}
.nav li.active{background:var(--green-dark)}

/* hero */
.hero{height:612px;background:linear-gradient(180deg,#6fb6e6 0%,#a7d6f2 45%,#cfe4a8 70%,#7fae4a 100%);position:relative}
.hero-caption{position:absolute;left:0;top:360px;background:rgba(0,60,110,.55);padding:22px 40px 24px 80px;color:var(--white)}
.hero-caption h1{font-family:"Roboto Condensed",sans-serif;font-size:38px;font-weight:700;letter-spacing:1px}
.hero-caption p{font-family:"Roboto Condensed",sans-serif;font-size:32px;margin-top:4px}
.dots{position:absolute;left:80px;bottom:30px;display:flex;gap:10px}
.dots i{width:12px;height:12px;border-radius:50%;background:rgba(255,255,255,.6)}
.dots i:first-child{background:var(--white)}

/* welcome */
.welcome{padding:44px 0 0;background:#f6f6f6;height:360px}
.welcome h2{text-align:center;font-size:30px;color:var(--heading);font-weight:500}
.welcome .lead{text-align:center;font-size:13px;line-height:21px;color:var(--muted);width:860px;margin:16px auto 0}
.features{display:flex;justify-content:space-between;margin-top:40px}
.feature{width:330px;display:flex;gap:18px}
.feature .box{width:76px;height:76px;flex:none;display:flex;align-items:center;justify-content:center}
.feature h3{font-size:17px;font-weight:700;color:var(--heading);letter-spacing:.5px}
.feature p{font-size:12px;line-height:19px;color:var(--muted);margin-top:6px}
.g{background:var(--green)}.y{background:var(--yellow)}.r{background:var(--red)}

/* about */
.about{height:410px;padding-top:56px}
.about .wrap{display:flex;gap:50px}
.screen{width:400px;height:290px;flex:none;background:linear-gradient(180deg,#e9e9e9,#cfcfcf)}
.about h2{font-size:24px;color:var(--heading);font-weight:500;margin-top:10px}
.about p{font-size:13px;line-height:21px;color:var(--muted);margin-top:14px}

/* services */
.services{background:var(--band);height:430px;padding-top:36px}
.cards{display:flex;justify-content:space-between}
.card{width:330px}
.card .photo{height:210px}
.card h3{font-size:16px;font-weight:700;color:var(--heading);margin-top:18px}
.card p{font-size:12px;line-height:19px;color:var(--muted);margin-top:8px}

/* partners */
.partners{height:130px;display:flex;align-items:center}
.partners .wrap{display:flex;justify-content:space-between}
.badge{width:130px;height:40px;background:#c9c9c9;border-radius:4px}

/* footer */
.footer{background:var(--green);height:190px;color:var(--white);padding-top:26px}
.footer .wrap{display:flex;justify-content:space-between}
.col{width:230px}
.col h4{font-size:14px;font-weight:700;letter-spacing:1px}
.col p,.col li{font-size:12px;line-height:19px;opacity:.9}
.col ul{list-style:none;margin-top:10px}
.col p{margin-top:10px}
.sub{display:flex;margin-top:12px}
.sub .field{width:150px;height:30px;background:var(--white);color:#aaa;font-size:12px;padding:7px 8px}
.sub .btn{width:80px;height:30px;background:var(--red);font-size:12px;display:flex;align-items:center;justify-content:center}
.social{display:flex;gap:8px;margin-top:14px}
.social i{width:26px;height:26px;border-radius:50%;background:var(--green-deep)}
.copyright{background:var(--green-deep);height:40px;display:flex;align-items:center;justify-content:center;color:var(--white);font-size:12px}
</style>
</head>
<body>

<header class="topbar">
  <div class="wrap">
    <div class="brand"><span class="dot"></span>LUMORA</div>
    <div class="top-contact">
      <span><i class="ico"><svg width="14" height="10" viewBox="0 0 14 10"><rect x="0.5" y="0.5" width="13" height="9" fill="none" stroke="#fff"/><path d="M0.5 0.5 L7 6 L13.5 0.5" fill="none" stroke="#fff"/></svg></i>info@lumoramail.com</span>
      <span><i class="ico"><svg width="12" height="12" viewBox="0 0 12 12"><path d="M2 1 L4.5 1 L5.5 4 L4 5 Q5 7.5 7 8 L8 6.5 L11 7.5 L11 10 Q6 11.5 2 6 Q0.5 3 2 1Z" fill="#fff"/></svg></i>0400 11 22 33</span>
      <div class="search">Search<svg width="14" height="14" viewBox="0 0 14 14"><circle cx="6" cy="6" r="4.5" fill="none" stroke="#aaa" stroke-width="1.5"/><path d="M9.5 9.5 L13 13" stroke="#aaa" stroke-width="1.5"/></svg></div>
    </div>
  </div>
</header>

<nav class="nav">
  <ul>
    <li class="active">HOME</li><li>STUDYVANE</li><li>EDUCATION</li><li>COURSES</li><li>CONTACT</li><li>ABOUT</li>
  </ul>
</nav>

<section class="hero" role="img" aria-label="Group of happy students jumping on a grassy field under a blue sky">
  <div class="hero-caption">
    <h1>LUMORA ONLINE EDUCATION</h1>
    <p>Neque porro quisquam est qui dolorem</p>
  </div>
  <div class="dots"><i></i><i></i><i></i><i></i></div>
</section>

<section class="welcome">
  <div class="wrap">
    <h2>WELCOME TO LUMORA!</h2>
    <p class="lead">Studyvane is a unique program that has been carefully crafted to provide the best learning outcomes for your employees. We connect you with the right providers and courses for your business. Our student support mentors guide every learner from enrolment to completion, so your people can study at home with confidence and grow their careers with accredited qualifications that truly matter to you.</p>
    <div class="features">
      <div class="feature">
        <div class="box g"><svg width="34" height="34" viewBox="0 0 34 34"><path d="M6 18 L14 26 L28 9" fill="none" stroke="#fff" stroke-width="4"/></svg></div>
        <div><h3>STUDYVANE</h3><p>For better relationships with your people, deliver programs based on skills and real goals.</p></div>
      </div>
      <div class="feature">
        <div class="box y"><svg width="34" height="34" viewBox="0 0 34 34"><rect x="5" y="7" width="24" height="16" fill="none" stroke="#fff" stroke-width="3"/><path d="M11 28 H23" stroke="#fff" stroke-width="3"/></svg></div>
        <div><h3>ONLINE COURSES</h3><p>Selected courses from trusted providers, studied online at a pace that suits every learner.</p></div>
      </div>
      <div class="feature">
        <div class="box r"><svg width="34" height="34" viewBox="0 0 34 34"><path d="M5 7 H29 V23 H14 L8 28 V23 H5Z" fill="none" stroke="#fff" stroke-width="3"/></svg></div>
        <div><h3>LET'S CHAT</h3><p>Our advisers listen to what your staff want to achieve and match them with providers.</p></div>
      </div>
    </div>
  </div>
</section>

<section class="about">
  <div class="wrap">
    <div class="screen" role="img" aria-label="Desktop computer screen showing the Lumora website"></div>
    <div>
      <h2>STUDYVANE</h2>
      <p>Studyvane is a unique program that has been carefully crafted to provide the best learning outcomes for your employees.</p>
      <p>We connect you and your business with the most appropriate approach and courses for training and growth.</p>
      <p>Our student support, mentoring and development programs ensure that your employees are receiving all the support they need to grow their career and importantly take what they learn back into the workplace.</p>
    </div>
  </div>
</section>

<section class="services">
  <div class="wrap cards">
    <div class="card">
      <div class="photo" role="img" aria-label="Business consultants meeting around a table" style="background:linear-gradient(135deg,#cfd8e0,#8fa3b5)"></div>
      <h3>LUMORA CONSULTING</h3>
      <p>We help HR teams find the right programs for leadership, business management and change within growing organisations.</p>
    </div>
    <div class="card">
      <div class="photo" role="img" aria-label="Open book with fanned pages" style="background:linear-gradient(135deg,#f4f1ea,#c9c2b3)"></div>
      <h3>COURSES</h3>
      <p>Business, health and wellbeing, digital and aviation courses chosen from quality providers only, ready to study online.</p>
    </div>
    <div class="card">
      <div class="photo" role="img" aria-label="Desk with study tools and colourful stationery" style="background:linear-gradient(135deg,#3d8f6a,#a8c46a)"></div>
      <h3>TAFE AND PRIVATE EDUCATION</h3>
      <p>Accredited qualifications from public and private providers, with support from first enquiry through to completion.</p>
    </div>
  </div>
</section>

<section class="partners">
  <div class="wrap">
    <i class="badge"></i><i class="badge"></i><i class="badge"></i><i class="badge"></i><i class="badge"></i><i class="badge"></i>
  </div>
</section>

<footer class="footer">
  <div class="wrap">
    <div class="col"><h4>LINKS</h4><ul><li>› Corporate Support</li><li>› Course Providers</li><li>› Resources</li><li>› Student FAQs</li></ul></div>
    <div class="col"><h4>ONLINE EDUCATION</h4><p>Study from home with flexible online courses and support from advisers every step of the way to completion.</p></div>
    <div class="col"><h4>GET IN TOUCH</h4><p>Address: 12 Harbour Lane, Springvale 3171<br>Phone: 0400 11 22 33<br>Email: info@lumoramail.com</p></div>
    <div class="col"><h4>NEWSLETTER</h4><p>Sign up for course news and updates.</p>
      <div class="sub"><div class="field">Email Address</div><div class="btn">Subscribe</div></div>
      <div class="social"><i></i><i></i><i></i></div>
    </div>
  </div>
</footer>
<div class="copyright">Copyright © 2014. All Rights Reserved</div>

</body>
</html>
```